business card

Business card for new business.
Red and black corporate colors.
Card can have an Indsutrial feel to it. Feel free to add Rust, Bolted steel, or graphics as you see fit. We provide highly specialized services to the below mentioned industries.
Keep information out of corners so that if I want I can choose rounded corners.
Information
- front. name - title - phone - email
- Rear
Refining - Rail - Infrastructure - Mining - Energy
Calgary - Edmonton - Fort McMurray - Revelstoke - Vancouver

```html
<!DOCTYPE html>
<html lang="en">
<head>
<meta charset="utf-8">
<title>Keelridge Business Card</title>
<link rel="stylesheet" href="https://fonts.googleapis.com/css2?family=Roboto:wght@400;500;700&display=swap">
<style>
  :root {
    --backdrop: #5b4838;
    --card-dark: #232323;
    --card-light: #f2f2f2;
    --brand-red: #e30613;
    --brand-grey: #8a8a8a;
    --text-light: #ffffff;
    --text-muted: #555555;
  }
  * { margin: 0; padding: 0; box-sizing: border-box; }
  html, body {
    width: 1200px; height: 960px; overflow: hidden;
    background: var(--backdrop);
    font-family: "Roboto", Arial, sans-serif;
  }
  .canvas { position: relative; width: 1200px; height: 960px; }
  .card { position: absolute; width: 600px; height: 344px; }
  .card-front { left: 314px; top: 113px; background: var(--card-dark); }
  .card-back  { left: 311px; top: 472px; background: var(--card-light); }

  .front-brand {
    position: absolute; right: 46px; top: 40px;
    display: flex; align-items: center; gap: 10px;
  }
  .brand-square { width: 18px; height: 18px; background: var(--brand-red); }
  .front-brand .brand-name {
    font-weight: 700; font-size: 40px; letter-spacing: 1px;
    color: var(--brand-grey); line-height: 1;
  }

  .holder { position: absolute; left: 42px; top: 189px; }
  .holder-name { font-weight: 700; font-size: 21px; color: var(--brand-red); line-height: 1; }
  .holder-title { font-weight: 500; font-size: 15px; color: var(--text-light); margin-top: 7px; line-height: 18px; }
  .contact { position: absolute; left: 42px; top: 244px; color: var(--text-light); font-size: 14px; line-height: 19px; }
  .rule-arrow { position: absolute; left: 42px; top: 284px; width: 514px; height: 10px; }
  .website {
    position: absolute; left: 42px; top: 294px;
    color: var(--text-light); font-size: 14px; letter-spacing: 7.6px;
  }

  .back-brand {
    position: absolute; left: 0; right: 0; top: 130px;
    display: flex; justify-content: center; align-items: center; gap: 12px;
  }
  .back-brand .brand-square { width: 26px; height: 26px; }
  .back-brand .brand-name { font-weight: 700; font-size: 44px; color: var(--brand-red); line-height: 1; letter-spacing: 1px; }

  .services {
    position: absolute; left: 0; right: 0; top: 257px;
    text-align: center; font-size: 14.5px; line-height: 18px; color: var(--text-muted);
  }
  .dot { color: var(--brand-red); padding: 0 3px; }
</style>
</head>
<body>
<div class="canvas">
  <section class="card card-front">
    <div class="front-brand">
      <span class="brand-square"></span>
      <span class="brand-name">KEELRIDGE</span>
    </div>
    <div class="holder">
      <p class="holder-name">DANA WHITFIELD</p>
      <p class="holder-title">CEO/FOUNDER</p>
    </div>
    <div class="contact">
      <p>604 555 0187</p>
      <p>info@keelridge.com</p>
    </div>
    <svg class="rule-arrow" viewBox="0 0 514 10" aria-hidden="true">
      <line x1="0" y1="5" x2="506" y2="5" stroke="#e30613" stroke-width="2"/>
      <polygon points="504,1.5 514,5 504,8.5" fill="#e30613"/>
    </svg>
    <p class="website">www.keelridge.com</p>
  </section>

  <section class="card card-back">
    <div class="back-brand">
      <span class="brand-square"></span>
      <span class="brand-name">KEELRIDGE</span>
    </div>
    <div class="services">
      <p>Fabrication<span class="dot">•</span>Pipelines<span class="dot">•</span>Utilities<span class="dot">•</span>Forestry</p>
      <p>Marine<span class="dot">•</span>Ashford Bay<span class="dot">•</span>Millbrook<span class="dot">•</span>Kestrel Falls</p>
      <p>Pinecrest<span class="dot">•</span>Stonehaven</p>
    </div>
  </section>
</div>
</body>
</html>
```